Auntie Verdict Billboard

I need a billboard designed for a Personal Injury Law firm. I need to simple not busy. I am attaching the following as suggestions to use. Need good colors that show up from Road Simple that can leave people associating injury lawyer with Auntie Verdict. Big picture of Dottie. Need Auntieverdict.com and 555-417-9038 to be big. possiblly let the emojis do the talking for personal injury and money settlement. Colors for logo should be similar to website auntieverdict.com
Updates

Billboard size. 10.5ft. X 36ft.

Target Market(s)

Car Accident Victims

Font styles to use
Sans Serif

Requirements
Must have
• Picture of Dottie. auntieverdict.com. 555-417-9038. message needs to be clear that she is a personal injury attorney. Clear simple message. Colors bold and visable to highway drivers
Should not have
• Busy ad.

```html
<!DOCTYPE html>
<html lang="en">
<head>
<meta charset="utf-8">
<title>Auntie Verdict Billboard</title>
<link rel="stylesheet" href="https://fonts.googleapis.com/css2?family=Playfair+Display:wght@700&family=Oswald:wght@700&family=Montserrat:wght@600;800&family=Open+Sans:wght@800&display=swap">
<style>
  :root {
    --navy: #111a2e;
    --red: #c01f2f;
    --white: #ffffff;
    --backdrop: #d9d9d9;
    --photo-tone: #3a3640;
    --photo-light: #eeeef0;
    --money-green: #7fbf3a;
  }
  * { margin: 0; padding: 0; box-sizing: border-box; }
  html, body { width: 1200px; height: 960px; overflow: hidden; }
  body { background: var(--backdrop); position: relative; }
  .billboard {
    position: absolute;
    left: 40px; top: 317px;
    width: 1336px; height: 390px;
    transform: scale(0.8383);
    transform-origin: 0 0;
    background: var(--white);
    overflow: hidden;
    box-shadow: 0 14px 30px rgba(0,0,0,0.25);
  }
  .shapes { position: absolute; inset: 0; }
  .portrait {
    position: absolute; left: 60px; top: 12px; width: 320px; height: 378px;
    background: linear-gradient(180deg, var(--photo-light) 0%, #b9a39a 30%, var(--photo-tone) 60%, var(--navy) 100%);
    border-radius: 140px 140px 0 0;
  }
  .url {
    position: absolute; left: 900px; top: 22px; width: 420px;
    text-align: center; color: var(--white);
    font: 600 19px/1 "Montserrat", sans-serif; letter-spacing: 4px;
    white-space: nowrap;
  }
  .url b { font-weight: 800; }
  .tagline {
    position: absolute; left: 535px; top: 50px;
    font: 700 34px/1 "Playfair Display", serif; color: var(--navy);
    white-space: nowrap;
  }
  .tagline .accent { color: var(--red); }
  .practice {
    position: absolute; left: 532px; top: 108px;
    font: 700 66px/1 "Oswald", sans-serif; color: var(--red);
    letter-spacing: -1px; white-space: nowrap;
  }
  .title {
    position: absolute; left: 530px; top: 180px;
    font: 800 76px/1 "Montserrat", sans-serif; color: var(--navy);
    letter-spacing: -2px; white-space: nowrap;
  }
  .settlement-art {
    position: absolute; left: 1066px; top: 74px; width: 190px; height: 118px;
    background: radial-gradient(ellipse at center, var(--money-green) 0%, #a8d86a 55%, var(--white) 75%);
  }
  .firm-name {
    position: absolute; left: 1004px; top: 216px;
    display: flex; align-items: center; gap: 8px;
    font: 600 19px/1 "Montserrat", sans-serif; color: var(--navy);
    letter-spacing: 1px; white-space: nowrap;
  }
  .firm-name .mark { width: 14px; height: 14px; background: var(--red); flex: none; }
  .phone {
    position: absolute; left: 498px; top: 285px; width: 800px;
    text-align: center; white-space: nowrap;
    font: 800 76px/1.1 "Open Sans", sans-serif; color: var(--white);
  }
</style>
</head>
<body>
  <section class="billboard">
    <svg class="shapes" viewBox="0 0 1336 390" width="1336" height="390" aria-hidden="true">
      <polygon points="868,0 1336,0 1336,60 893,60" fill="var(--navy)"/>
      <path d="M440,272 L1336,272 L1336,390 L370,390 C410,355 430,315 440,272 Z" fill="var(--navy)"/>
      <path d="M395,0 L480,0 C505,150 470,300 380,390 L358,390 C440,300 455,150 395,0 Z" fill="var(--red)"/>
      <path d="M395,0 C455,150 440,300 358,390 L350,390 C430,300 445,150 385,0 Z" fill="var(--navy)"/>
    </svg>
    <div class="portrait" role="img" aria-label="Photo of the attorney in a dark blazer"></div>
    <div class="url">WWW.<b>AUNTIEVERDICT</b>.COM</div>
    <div class="tagline">Your Lady for <span class="accent">Justice</span></div>
    <div class="practice">PERSONAL INJURY</div>
    <div class="title">ATTORNEY</div>
    <div class="settlement-art" role="img" aria-label="Cartoon money bundle with hands offering keys"></div>
    <div class="firm-name"><span class="mark"></span>VERDICT LAW FIRM PLLC</div>
    <div class="phone">CALL: 555-417-9038</div>
  </section>
</body>
</html>
```